Web design for Crowdfunding site HopeWingsRally.com

We need a web design for christian crowdfunding website. Here is the challenge: We need responsive layout that is targeted first in iPad size of screen. It should also scale somehow down to iPhone size of screens. Web layout can be about the same size as iPad screen.

Screens should work so that main page scrolls not but only certain part of the screen scrolls and always one "page" at time. We can implement these "scrolls" then later with javascript but now we need only design. The challenge is to create this kind of hybrid website / app look.

Target is at first to raise funds to orphan people needing about $40 per month for their living and education. There is always some organization which takes care of these kids. Later there will be other christian missions included. At first we are looking to find monthly supporters.

You can be as creative as you want :) As you see from the look and feel sector, I am not looking any same traditional look which many "help kids" sites have. I am looking to reach now younger generation and therefore iPad and mobile are the main screen sizes.

Inspirational designs:
- https://example-gallery.test/profiles/studiofernlake/designs/482716?from=%2Fbrowse%2Fxhr%2Fdesigns%3Fcategory%3Dmobile-app-design
- http://www.artpoolhub.test/design/8261047 Clear, simple visuals
- http://www.artpoolhub.test/design/7394215 Header
- http://www.artpoolhub.test/design/6048392 Contrast in the colors, i think is powerfull

Some terms could be: Kids play, kids are learning (in the school). No static posture but living like kids are. I wonder also how we could also add little bit gaming style even though the question is of reali life of real people. Giving should be rewarding.

Target Market(s)

People who want help other people.

Industry/Entity Type

Christian

Number of Pages Required

4 page

Requirements
Must have
• Homepage. Mission page (In my wireframes it was one kid).
Nice to have
• Other pages and some idea how to scroll. 4 pages is no must. If you feel easy, please give first some draft and I give comments on that.

```html
<!DOCTYPE html>
<html lang="en">
<head>
<meta charset="utf-8">
<title>HopeWingsRally – Mission</title>
<link rel="stylesheet" href="https://fonts.googleapis.com/css2?family=Roboto:ital,wght@0,400;0,500;0,700;1,500&family=Open+Sans:wght@400;600&display=swap">
<style>
:root{
  --black:#000;
  --ink:#111;
  --yellow:#ffc000;
  --yellow-hi:#ffd800;
  --orange:#ffa000;
  --red:#e2211c;
  --page:#f4f4f4;
  --white:#fff;
  --text:#555;
}
*{box-sizing:border-box;margin:0;padding:0}
html,body{width:1200px;height:786px;overflow:hidden}
body{background:var(--page);font-family:"Roboto",Arial,sans-serif;color:var(--ink);position:relative}

/* header */
.site-header{position:absolute;top:0;left:0;width:1200px;height:81px;background:var(--black);border-top:3px solid var(--yellow)}
.nav-left{position:absolute;left:127px;top:28px;display:flex;align-items:center;color:var(--white);font-size:13px;font-weight:500}
.nav-left .menu-icon{margin-right:25px}
.nav-left .search-icon{margin-left:26px}
.brand{position:absolute;left:0;right:0;top:20px;text-align:center;color:var(--yellow);font-size:29px;font-weight:700;letter-spacing:-.5px}
.nav-right{position:absolute;right:127px;top:31px;display:flex;gap:40px;color:var(--white);font-size:13px;font-weight:500}
.nav-right span{display:flex;align-items:center;gap:5px}

/* mission card */
.mission-card{position:absolute;left:127px;top:107px;width:632px;height:574px;background:var(--white);box-shadow:0 0 3px rgba(0,0,0,.12);overflow:hidden}
.mission-title{height:55px;padding:19px 0 0 21px;font-size:17px;font-weight:500}
.tabs{display:flex;height:42px}
.tab{flex:1;display:flex;align-items:center;justify-content:center;font-size:14px;font-weight:500;color:var(--white)}
.tab.story{background:linear-gradient(var(--yellow-hi),var(--orange))}
.tab.updates{background:var(--black)}
.tab.comments{background:linear-gradient(#333,#111)}
.story-body{position:relative;padding:24px 18px 0 67px}
.timeline{position:absolute;left:34px;top:38px;width:5px;height:398px;background:var(--ink)}
.dot{position:absolute;left:23px;width:27px;height:27px;border-radius:50%;background:var(--ink);display:flex;align-items:center;justify-content:center}
.dot.active{background:var(--yellow)}
.story-text{font-family:"Open Sans",Arial,sans-serif;font-size:12px;line-height:26px;color:var(--text);letter-spacing:-.05px}
.story-photo{height:196px;margin:18px 5px 17px 0;background:linear-gradient(100deg,#7a5a3d 0%,#a9845f 35%,#c9d3e0 70%,#8a97a8 100%)}

/* support panel */
.support-panel{position:absolute;left:783px;top:107px;width:290px;height:574px;background:var(--yellow);box-shadow:0 0 3px rgba(0,0,0,.12)}
.profile{height:109px;background:linear-gradient(#3a3a3a,#000);position:relative;color:var(--white)}
.avatar{position:absolute;left:21px;top:14px;width:60px;height:60px;border-radius:50%;background:var(--white)}
.profile-name{position:absolute;left:95px;top:17px;font-size:17.5px;font-weight:500}
.profile-meta{position:absolute;left:95px;top:50px;display:flex;gap:10px;font-size:13px;font-style:italic;font-weight:500;line-height:21px}
.support-row{display:flex;align-items:center;padding:8px 0 0 21px;font-size:14px;font-weight:500;height:44px}
.support-row .label{margin-right:8px}
.person{width:25px;height:25px;border:1.5px solid var(--ink);border-radius:50%;display:flex;align-items:center;justify-content:center;margin-right:11px}
.pledge-box{margin:8px 19px 0 21px;height:160px;background:var(--white);position:relative}
.pledge-head{position:absolute;left:12px;top:11px;font-size:14px;font-weight:500}
.pledge-close{position:absolute;right:9px;top:10px}
.donut{position:absolute;left:12px;top:42px}
.donut-value{position:absolute;left:12px;top:42px;width:104px;height:104px;display:flex;align-items:center;justify-content:center;font-size:21px}
.pledge-stats{position:absolute;left:128px;top:58px;font-size:12px;color:var(--text);line-height:26px}
.pledge-stats strong{color:var(--ink);font-weight:700;font-size:13px}
.pledge-stats .monthly{display:flex;align-items:center;gap:6px}
.participate-title{padding:10px 0 0 21px;font-size:14px;font-weight:500;height:34px}
.options{list-style:none;margin:0 19px 0 21px}
.option{height:33px;margin-bottom:8px;background:var(--white);border-radius:2px;display:flex;align-items:center;padding:0 12px 0 4px;font-size:12px;color:#444;white-space:nowrap}
.option .swatch{flex:none;width:36px;height:26px;background:var(--red);border-radius:2px;margin-right:12px}
.option .name{flex:1}
.option .hint{color:#999;font-size:11px}
.option svg{flex:none}

/* footer */
.site-footer{position:absolute;left:0;top:710px;width:1200px;height:76px;background:var(--black);color:var(--white);font-family:"Open Sans",Arial,sans-serif;font-size:12px}
.copyright{position:absolute;left:127px;top:30px}
.copyright .hl{color:var(--yellow)}
.follow{position:absolute;left:837px;top:30px;display:flex;align-items:center}
.follow .social{width:10px;height:10px;border-radius:50%;background:#888;margin-left:26px}
.follow .social.first{background:var(--yellow);margin-left:12px}
</style>
</head>
<body>

<header class="site-header">
  <div class="nav-left">
    <svg class="menu-icon" width="22" height="18" viewBox="0 0 22 18" fill="#fff"><rect x="0" y="0" width="4" height="4" rx="1"/><rect x="6" y="0" width="16" height="4" rx="1"/><rect x="0" y="7" width="4" height="4" rx="1"/><rect x="6" y="7" width="16" height="4" rx="1"/><rect x="0" y="14" width="4" height="4" rx="1"/><rect x="6" y="14" width="16" height="4" rx="1"/></svg>
    <span>SEE THE MISSIONS</span>
    <svg class="search-icon" width="19" height="19" viewBox="0 0 19 19" fill="none" stroke="#fff" stroke-width="1.8"><circle cx="8" cy="8" r="6.5"/><line x1="12.8" y1="12.8" x2="18" y2="18"/></svg>
  </div>
  <div class="brand">HopeWingsRally</div>
  <div class="nav-right">
    <span><svg width="10" height="12" viewBox="0 0 10 12" fill="#fff"><path d="M2 5V3.5a3 3 0 0 1 6 0V5" fill="none" stroke="#fff" stroke-width="1.6"/><rect x="0" y="5" width="10" height="7" rx="1"/></svg>LOG IN</span>
    <span><svg width="14" height="12" viewBox="0 0 14 12" fill="#fff"><path d="M0 4.5h5V1.5l5 4.5-5 4.5V7.5H0z"/><path d="M8 0h5a1 1 0 0 1 1 1v10a1 1 0 0 1-1 1H8v-2h4V2H8z"/></svg>SIGN UP</span>
  </div>
</header>

<main>
  <section class="mission-card">
    <h1 class="mission-title">Mission : Orphan Maria,11Y</h1>
    <nav class="tabs">
      <div class="tab story">Story</div>
      <div class="tab updates">Updates</div>
      <div class="tab comments">Comments</div>
    </nav>
    <div class="story-body">
      <div class="timeline"></div>
      <div class="dot" style="top:27px"><svg width="11" height="11" viewBox="0 0 11 11" fill="#fff"><path d="M0 4.3h6V1l5 4.5L6 10V6.7H0z"/></svg></div>
      <div class="dot active" style="top:226px"><svg width="11" height="11" viewBox="0 0 11 11" fill="#fff"><path d="M0 4.3h6V1l5 4.5L6 10V6.7H0z"/></svg></div>
      <div class="dot" style="top:424px"><svg width="11" height="11" viewBox="0 0 11 11" fill="#fff"><path d="M0 4.3h6V1l5 4.5L6 10V6.7H0z"/></svg></div>
      <p class="story-text">Sed ut perspiciatis unde omnis iste natus error sit voluptatem accusantium doloremque laudaer ntium, totam rem aperiam, eaque ipsa quae ab illo inventore veritatis et quasi architecto beatae vitae dicta sunt explicabo. Nemo enim ipsam voluptatem quia voluptas sit aspernatur aut odit aut fugit, sed quia consequuntur magni dolores eos qui ratione...</p>
      <div class="story-photo" role="img" aria-label="Photo of smiling children eating lunch together at a school table"></div>
      <p class="story-text">Led ut perspiciatis unde omnis iste natus error sit voluptatem accusantium doloremque laudaer ntium, totam rem aperiam, eaque ipsa quae ab illo inventore veritatis et quasi architecto beatae vitae dicta sunt explicabo. Nemo enim ipsam voluptatem quia voluptas sit aspernatur aut odit aut fugit, sed quia consequuntur magni dolores eos qui ratione...</p>
    </div>
  </section>

  <aside class="support-panel">
    <div class="profile">
      <div class="avatar"></div>
      <div class="profile-name">Name : Maria,11Y</div>
      <div class="profile-meta">
        <svg width="14" height="20" viewBox="0 0 14 20"><path d="M7 0a7 7 0 0 0-7 7c0 5 7 13 7 13s7-8 7-13a7 7 0 0 0-7-7z" fill="#ffc000"/><circle cx="7" cy="7" r="2.8" fill="#111"/></svg>
        <div>Kalkutta<br>Organization : Jacob</div>
      </div>
    </div>

    <div class="support-row">
      <span class="label">Support</span>
      <span class="person"><svg width="10" height="14" viewBox="0 0 10 14" fill="#111"><circle cx="5" cy="2" r="2"/><path d="M2 5h6l1.5 5H7v4H3v-4H.5z"/></svg></span>
      <span class="person"><svg width="10" height="14" viewBox="0 0 10 14" fill="#111"><circle cx="5" cy="2" r="2"/><path d="M2 5h6v5H7v4H3v-4H2z"/></svg></span>
      <span class="person"><svg width="10" height="14" viewBox="0 0 10 14" fill="#111"><circle cx="5" cy="2" r="2"/><path d="M2 5h6l1.5 5H7v4H3v-4H.5z"/></svg></span>
      <span class="person"><svg width="10" height="14" viewBox="0 0 10 14" fill="#111"><circle cx="5" cy="2" r="2"/><path d="M2 5h6v5H7v4H3v-4H2z"/></svg></span>
      <span class="person"><svg width="10" height="14" viewBox="0 0 10 14" fill="#111"><circle cx="5" cy="2" r="2"/><path d="M2 5h6l1.5 5H7v4H3v-4H.5z"/></svg></span>
      <svg width="10" height="16" viewBox="0 0 10 16" fill="none" stroke="#111" stroke-width="2.2"><path d="M2 1l6 7-6 7"/></svg>
    </div>

    <div class="pledge-box">
      <div class="pledge-head">My Support is now $5 / month</div>
      <svg class="pledge-close" width="19" height="19" viewBox="0 0 19 19"><circle cx="9.5" cy="9.5" r="9.5" fill="#e2211c"/><path d="M6 6l7 7M13 6l-7 7" stroke="#fff" stroke-width="1.8"/></svg>
      <svg class="donut" width="104" height="104" viewBox="0 0 104 104" fill="none" stroke-width="7"><circle cx="52" cy="52" r="48" stroke="#111"/><path d="M52 100A48 48 0 0 1 52 4" stroke="#e2211c"/></svg>
      <div class="donut-value">45%</div>
      <div class="pledge-stats">
        <strong>$15 Given</strong><br>
        of total $35 Needed<br>
        <span class="monthly"><svg width="18" height="18" viewBox="0 0 18 18" fill="none" stroke="#111" stroke-width="1.5"><rect x="1" y="3" width="16" height="14"/><path d="M1 7h16M5 1v4M13 1v4"/><path d="M4 10h2M8 10h2M12 10h2M4 13h2M8 13h2M12 13h2" stroke-width="1.8"/></svg>Per Month Need</span>
      </div>
    </div>

    <div class="participate-title">Participate</div>
    <ul class="options">
      <li class="option"><span class="swatch"></span><span class="name">I,am in, $1 / month</span><svg width="21" height="19" viewBox="0 0 21 19" fill="none" stroke="#e2211c" stroke-width="1.4"><path d="M0 1h3l3 11h11l3-8H5"/><path d="M7 8h11"/><circle cx="8" cy="16" r="1.6"/><circle cx="16" cy="16" r="1.6"/></svg></li>
      <li class="option"><span class="swatch"></span><span class="name">Increased, $5 / month</span><svg width="21" height="19" viewBox="0 0 21 19" fill="none" stroke="#e2211c" stroke-width="1.4"><path d="M0 1h3l3 11h11l3-8H5"/><path d="M7 8h11"/><circle cx="8" cy="16" r="1.6"/><circle cx="16" cy="16" r="1.6"/></svg></li>
      <li class="option"><span class="swatch"></span><span class="name">Decent Help, $10 / month</span><svg width="21" height="19" viewBox="0 0 21 19" fill="none" stroke="#e2211c" stroke-width="1.4"><path d="M0 1h3l3 11h11l3-8H5"/><path d="M7 8h11"/><circle cx="8" cy="16" r="1.6"/><circle cx="16" cy="16" r="1.6"/></svg></li>
      <li class="option"><span class="swatch"></span><span class="name">Whole Kid, $35 / month</span><svg width="21" height="19" viewBox="0 0 21 19" fill="none" stroke="#e2211c" stroke-width="1.4"><path d="M0 1h3l3 11h11l3-8H5"/><path d="M7 8h11"/><circle cx="8" cy="16" r="1.6"/><circle cx="16" cy="16" r="1.6"/></svg></li>
      <li class="option"><span class="swatch"></span><span class="name">My Amount $ : ( <span class="hint">Enter Amount</span> )</span><svg width="21" height="19" viewBox="0 0 21 19" fill="none" stroke="#e2211c" stroke-width="1.4"><path d="M0 1h3l3 11h11l3-8H5"/><path d="M7 8h11"/><circle cx="8" cy="16" r="1.6"/><circle cx="16" cy="16" r="1.6"/></svg></li>
    </ul>
  </aside>
</main>

<footer class="site-footer">
  <div class="copyright">COPYRIGHTS © 2016 . <span class="hl">HOPEWINGSRALLY</span> | ALLRIGHTS RESERVED.</div>
  <div class="follow">
    <span>FOLLOW US :</span>
    <span class="social first"></span>
    <span class="social"></span>
    <span class="social"></span>
    <span class="social"></span>
    <span class="social"></span>
  </div>
</footer>

</body>
</html>
```